Corportate Power Point Template

We need a corporate PPT Design for our startup Big Data company.

Basically, our company will ingest, analyze and generate dynamic Dashboards with data consumed from different sources like Social Networks, Enterprise Legacy Systems such as e-Commerce, ERP, CRM and others.

Company is headquartered in Brazil, but will have a global presence.

Industry/Entity Type

It Company

```html
<!DOCTYPE html>
<html lang="en">
<head>
<meta charset="UTF-8">
<title>Project Title Here</title>
<link rel="stylesheet" href="https://fonts.googleapis.com/css2?family=Saira+Semi+Condensed:wght@400;500;600&family=Roboto:wght@400;500&display=swap">
<style>
  :root {
    --accent: #f47b2a;
    --heading-red: #e8380d;
    --title-dark: #3a3a3a;
    --body-text: #555555;
    --footer-text: #333333;
    --rule: #dddddd;
    --bg: #fdfbf9;
  }
  * { margin: 0; padding: 0; box-sizing: border-box; }
  html, body { width: 1200px; height: 900px; overflow: hidden; }
  body { background: var(--bg); font-family: "Saira Semi Condensed", sans-serif; }

  .slide { position: relative; width: 1200px; height: 900px; overflow: hidden; background: var(--bg); }

  .backdrop {
    position: absolute; inset: 0;
    background:
      radial-gradient(ellipse 520px 360px at 180px 120px, rgba(250,200,160,0.45), rgba(250,200,160,0) 70%),
      linear-gradient(90deg, rgba(255,255,255,0) 55%, rgba(225,225,228,0.35) 100%);
  }

  .title-bar {
    position: absolute; left: 0; top: 36px; width: 12px; height: 72px; background: var(--accent);
  }
  .slide-title {
    position: absolute; left: 34px; top: 28px;
    font-size: 53px; font-weight: 600; letter-spacing: 1px; line-height: 1.5;
    color: var(--title-dark);
  }
  .slide-title .highlight { color: var(--accent); }

  .column { position: absolute; top: 210px; width: 483px; }
  .column.left { left: 64px; }
  .column.right { left: 633px; }

  .column h2 {
    font-family: "Roboto", sans-serif; font-weight: 500;
    font-size: 29px; color: var(--heading-red); line-height: 1.2;
    margin-bottom: 22px;
  }
  .column p {
    font-size: 20px; line-height: 36px; color: var(--body-text);
    text-align: justify; letter-spacing: 0.4px;
    margin-bottom: 36px;
  }

  .footer-rule {
    position: absolute; left: 0; right: 0; top: 817px; height: 1px; background: var(--rule);
  }
  .presenter {
    position: absolute; left: 12px; top: 852px;
    font-size: 19px; color: var(--footer-text);
  }
  .presenter .name { color: var(--accent); }

  .brand {
    position: absolute; right: 14px; top: 838px;
    display: flex; align-items: center; gap: 10px;
  }
  .brand-mark { width: 22px; height: 22px; background: var(--accent); }
  .brand-name {
    font-size: 38px; font-weight: 500; color: var(--accent); line-height: 1;
  }
</style>
</head>
<body>
  <main class="slide">
    <div class="backdrop" role="img" aria-label="Soft orange and grey tiled background texture"></div>

    <div class="title-bar"></div>
    <h1 class="slide-title"><span class="highlight">Project</span> Title Here</h1>

    <section class="column left">
      <h2>Lorem ipsum dolor sit ipsum</h2>
      <p>Lorem ipsum dolor sit ipsum Lorem ipsum dolor sit ipsum Lorem ipsum dolor sit ipsum Lorem ipsum dolor sit ipsum lorem ipsum dolor sit ipsum Lorem ipsum dolor sit ipsum Lorem ipsum dolor sit ipsum</p>
      <p>Lorem ipsum dolor sit ipsum Lorem ipsum dolor sit ipsum Lorem ipsum dolor sit ipsum Lorem ipsum dolor sit ipsum lorem ipsum dolor sit ipsum Lorem ipsum dolor sit ipsum Lorem ipsum dolor sit ipsum Lorem ipsum dolor sit ipsum</p>
    </section>

    <section class="column right">
      <h2>Lorem ipsum dolor sit ipsum</h2>
      <p>Lorem ipsum dolor sit ipsum Lorem ipsum dolor sit ipsum Lorem ipsum dolor sit ipsum Lorem ipsum dolor sit ipsum lorem ipsum dolor sit ipsum Lorem ipsum dolor sit ipsum Lorem ipsum dolor sit ipsum</p>
      <p>Lorem ipsum dolor sit ipsum Lorem ipsum dolor sit ipsum Lorem ipsum dolor sit ipsum Lorem ipsum dolor sit ipsum lorem ipsum dolor sit ipsum Lorem ipsum dolor sit ipsum Lorem ipsum dolor sit ipsum Lorem ipsum dolor sit ipsum</p>
    </section>

    <div class="footer-rule"></div>
    <p class="presenter">Persentatator Name : <span class="name">Marco Ferreira</span></p>

    <div class="brand">
      <span class="brand-mark"></span>
      <span class="brand-name">Vantor Data</span>
    </div>
  </main>
</body>
</html>
```